*YO!!! Designers Needed!!* Front Page Cover Needed for a $$Billion Dollar$$ Company

We are a manufacturer of aluminum electrolytic capacitors. We are looking to create a front page cover that will be used on our annual report. We are a publicly listed company and work with many Meridex 400 companies, so your work will be viewed by the BIG GUNS and EXECUTIVES around the WORLD! If selected, you may be selected for additional work.

The front page cover should be unique. If elegance, modern, bling, and creativity somehow got together and had a child, that's what the cover page would look like!

Inspired Examples attached. Check them out!

www.brovanta.com

Font styles to use
Sans Serif

Requirements
Must have
• 1. Must include the attached logo. Logo size, color, and placement are at your discretion.

2. Should include the text, '2020 Annual Report'

3. The design should incorporate the use of foil and/or be embossed. The foil can be part of the design or can be the full page. See various examples attached for reference.

4. Shall be in A4 size and vertical orientation.
Nice to have
• Feel free to add any icons or stock photos (for example capacitors or circuit boards) if needed.

Be creative here and don't be afraid to be bold! The end product will be printed and budget is not a limiting factor, so feel free to make it extravagant if needed.

Our slogan is "Think Ahead". This slogan can or cannot be part of the theme.

```html
<!DOCTYPE html>
<html lang="en">
<head>
<meta charset="utf-8">
<title>Brovanta 2020 Annual Report Cover</title>
<link rel="stylesheet" href="https://fonts.googleapis.com/css2?family=Montserrat:wght@200;400;700;800&display=swap">
<style>
  :root {
    --backdrop: #5a5a5a;
    --paper: #f6f6f6;
    --frame-black: #262626;
    --teal-light: #2ee6d9;
    --teal-deep: #14c2b8;
    --ink: #2b2b2b;
    --banner: #bff3ee;
    --foil-light: #f2f2f2;
    --foil-mid: #c9c9c9;
    --foil-dark: #9a9a9a;
    --url-grey: #5c5c5c;
  }
  * { margin: 0; padding: 0; box-sizing: border-box; }
  html, body { width: 900px; height: 1200px; overflow: hidden; }
  body {
    background: var(--backdrop);
    font-family: "Montserrat", sans-serif;
    position: relative;
  }
  .cover {
    position: absolute;
    left: 105px; top: 110px;
    width: 690px; height: 980px;
    background: var(--paper);
    overflow: hidden;
  }
  .frame-band {
    position: absolute;
    left: 0; top: 0;
    width: 560px; height: 610px;
    background: var(--frame-black);
  }
  .teal-panel {
    position: absolute;
    left: 34px; top: 34px;
    width: 620px; height: 600px;
    background: linear-gradient(150deg, var(--teal-deep) 0%, var(--teal-light) 55%, var(--teal-deep) 100%);
  }
  .headline {
    position: absolute;
    left: 150px; top: 250px;
    color: var(--ink);
    line-height: 0.9;
  }
  .headline-think {
    display: block;
    font-weight: 200;
    font-size: 74px;
    letter-spacing: 2px;
  }
  .headline-ahead {
    display: block;
    font-weight: 800;
    font-size: 92px;
    letter-spacing: 1px;
  }
  .report-banner {
    position: absolute;
    left: 150px; top: 445px;
    padding: 8px 22px;
    background: var(--banner);
    color: var(--ink);
    font-size: 32px;
    font-weight: 400;
    white-space: nowrap;
  }
  .report-banner .year { font-weight: 800; }
  .foil-photo {
    position: absolute;
    left: 250px; top: 560px;
    width: 440px; height: 320px;
    background: linear-gradient(135deg, var(--foil-light) 0%, var(--foil-mid) 40%, var(--foil-light) 60%, var(--foil-dark) 100%);
  }
  .brand-name {
    position: absolute;
    left: 250px; top: 686px;
    width: 440px;
    text-align: center;
    color: var(--ink);
    font-size: 64px;
    font-weight: 700;
    letter-spacing: 1px;
    line-height: 1;
  }
  .site-url {
    position: absolute;
    left: 0; right: 0; top: 920px;
    text-align: center;
    color: var(--url-grey);
    font-size: 18px;
    font-weight: 700;
    letter-spacing: 8px;
  }
</style>
</head>
<body>
  <main class="cover">
    <div class="frame-band"></div>
    <section class="teal-panel"></section>
    <h1 class="headline">
      <span class="headline-think">THINK</span>
      <span class="headline-ahead">AHEAD</span>
    </h1>
    <p class="report-banner"><span class="year">2020</span> Annual Report</p>
    <div class="foil-photo" role="img" aria-label="Hands unrolling a sheet of aluminium foil from a roll"></div>
    <p class="brand-name">Brovanta</p>
    <p class="site-url">www.brovanta.com</p>
  </main>
</body>
</html>
```